FinTech company looking to revamp and expand client-facing interface for our financial models

Pellworth Engines currently has a very simple website that allows clients to interact with our financial models. We are looking to completely redesign the current site and add several extra pages to provide extra functionality. We want the design to have a modern, slick feel, that will work on both a desktop or a tablet. It should be straightforward for clients to move between different pages at any time, and clear from the layout how to interact with the more advanced features. We have included screenshots of existing pages in the attached design brief, as well as sketches of the functionality required by the new pages, but can't provide a direct link to the current site.
Target Market(s)
Professional investors that will be paying to access the interface
Industry/Entity Type
Finance
Number of Pages Required
4 page
Colors
Designer to choose colors to be used in the design.
Look and feel
Each slider illustrates characteristics of the customer's brand and the style your logo design should communicate.

```html
<!DOCTYPE html>
<html lang="en">
<head>
<meta charset="utf-8">
<title>Pellworth Engines — Models</title>
<link rel="stylesheet" href="https://fonts.googleapis.com/css2?family=Arimo:wght@400;700&family=Montserrat:wght@600;700&family=Open+Sans:wght@400;700&display=swap">
<style>
  :root {
    --ink: #111111;
    --navy: #0d2436;
    --muted-dot: #8a8a8a;
    --tab-bg: #e4e4e4;
    --tab-border: #9a9a9a;
    --row-bg: #fcfcfc;
    --row-line: #9c9c9c;
    --positive: #22b022;
    --negative: #e0201c;
    --chart-bg: #222222;
    --chart-fill: #3a3a3a;
    --chart-grid: #4a4a4a;
    --dark-bar: #222222;
    --card-line: #d0d0d0;
    --page: #ffffff;
  }
  * { box-sizing: border-box; margin: 0; padding: 0; }
  html, body { width: 1200px; height: 750px; overflow: hidden; background: var(--page); }
  .canvas { position: relative; width: 1200px; height: 750px; color: var(--ink); font-family: "Arimo", Arial, sans-serif; }

  .range-picker { position: absolute; top: 27px; left: 15px; display: flex; gap: 0; font-family: "Montserrat", sans-serif; font-weight: 700; font-size: 14px; }
  .range { position: absolute; display: flex; align-items: center; gap: 8px; white-space: nowrap; color: #333; }
  .range::before { content: ""; width: 9px; height: 9px; border-radius: 50%; background: var(--muted-dot); }
  .range.is-active { color: var(--navy); }
  .range.is-active::before { background: var(--ink); }

  .main-nav { position: absolute; top: 28px; left: 0; font-family: "Montserrat", sans-serif; font-weight: 600; font-size: 17px; }
  .nav-link { position: absolute; white-space: nowrap; color: #1a1a1a; }
  .nav-link.is-current { color: var(--navy); font-weight: 700; }
  .nav-underline { position: absolute; left: 671px; top: 51px; width: 74px; height: 2.5px; background: var(--navy); border-radius: 1px; }

  .model-panel { position: absolute; left: 108px; top: 262px; width: 483px; }
  .model-tabs { display: flex; height: 42px; background: var(--tab-bg); }
  .model-tab { font-weight: 700; font-size: 13.5px; display: flex; align-items: center; padding-left: 20px; }
  .model-tab.is-active { width: 234px; border: 1px solid var(--tab-border); background: var(--tab-bg); }
  .model-tab.is-idle { flex: 1; padding-left: 26px; }
  .model-row { position: relative; display: flex; align-items: center; background: var(--row-bg); border-bottom: 1px solid var(--row-line); }
  .model-name { height: 41px; padding-left: 20px; font-size: 12.5px; }
  .selected-pill { position: absolute; right: 14px; top: 14px; width: 39px; height: 12px; border: 1px solid #555; border-radius: 6px; font-size: 5.5px; display: flex; align-items: center; justify-content: center; }
  .param-row { height: 42px; font-size: 10px; font-weight: 700; padding-left: 21px; }
  .param-row.tall { height: 43px; }
  .param-value { position: absolute; left: 260px; font-weight: 400; font-size: 9.5px; }
  .positive { color: var(--positive); }
  .negative { color: var(--negative); }
  .run-button { position: absolute; left: 535px; top: 533px; width: 53px; height: 20px; border: 0; border-radius: 3px; background: var(--ink); color: #fff; font-family: "Arimo", sans-serif; font-size: 10.5px; }

  .pnl-chart { position: absolute; left: 752px; top: 262px; width: 336px; height: 187px; border-radius: 5px; overflow: hidden; background: var(--chart-bg); }
  .axis-label { position: absolute; font-family: "Open Sans", sans-serif; font-weight: 700; font-size: 9px; color: #333; }
  .axis-y { left: 722px; top: 350px; transform: rotate(-90deg); font-size: 10px; }

  .stats { position: absolute; left: 834px; top: 503px; width: 255px; font-family: "Open Sans", sans-serif; }
  .stats-header { height: 25px; background: var(--dark-bar); color: #fff; font-weight: 700; font-size: 10.5px; display: flex; align-items: center; justify-content: space-between; padding: 0 8px 0 6px; border-radius: 2px; }
  .stats-caret { width: 0; height: 0; border-left: 3px solid transparent; border-right: 3px solid transparent; border-top: 3px solid #bbb; }
  .stats-table { margin-top: 5px; border: 1px solid var(--card-line); border-radius: 2px; box-shadow: 0 1px 2px rgba(0,0,0,.12); }
  .stat-row { position: relative; height: 41.5px; display: flex; align-items: center; padding-left: 28px; font-weight: 700; font-size: 10.5px; background: var(--row-bg); border-bottom: 1px solid #9a9a9a; }
  .stat-row:last-child { border-bottom: 0; }
  .stat-value { position: absolute; left: 173px; font-weight: 400; font-size: 8.5px; }
</style>
</head>
<body>
<div class="canvas">
  <div class="range-picker" aria-label="Time range">
    <span class="range is-active" style="left:0">250D</span>
    <span class="range" style="left:100px">83D</span>
    <span class="range" style="left:201px">24D</span>
  </div>

  <nav class="main-nav">
    <span class="nav-link is-current" style="left:674px">models</span>
    <span class="nav-link" style="left:818px">sensitivities</span>
    <span class="nav-link" style="left:1002px">favourites</span>
  </nav>
  <div class="nav-underline"></div>

  <section class="model-panel">
    <div class="model-tabs">
      <div class="model-tab is-active">Model 1</div>
      <div class="model-tab is-idle">Model 2</div>
    </div>
    <div class="model-row model-name">Model : Model name<span class="selected-pill">Selected</span></div>
    <div class="model-row param-row tall">Parameters</div>
    <div class="model-row param-row">Entry<span class="param-value positive">0.5</span></div>
    <div class="model-row param-row tall">Exit<span class="param-value negative">-0.3</span></div>
    <div class="model-row param-row">Lookback<span class="param-value positive">5</span></div>
  </section>
  <button class="run-button">Run</button>

  <span class="axis-label axis-y">PNL</span>
  <div class="pnl-chart">
    <svg width="336" height="187" viewBox="0 0 403 224" preserveAspectRatio="none">
      <g stroke="var(--chart-grid)" stroke-width="1" stroke-dasharray="2 2">
        <line x1="50" y1="0" x2="50" y2="224"/><line x1="101" y1="0" x2="101" y2="224"/>
        <line x1="151" y1="0" x2="151" y2="224"/><line x1="201" y1="0" x2="201" y2="224"/>
        <line x1="252" y1="0" x2="252" y2="224"/><line x1="302" y1="0" x2="302" y2="224"/>
        <line x1="352" y1="0" x2="352" y2="224"/>
        <line x1="0" y1="38" x2="403" y2="38"/><line x1="0" y1="88" x2="403" y2="88"/>
        <line x1="0" y1="138" x2="403" y2="138"/><line x1="0" y1="186" x2="403" y2="186"/>
      </g>
      <path fill="var(--chart-fill)" fill-opacity="0.85" d="M0 40 L15 70 L22 60 L38 75 L48 110 L65 145 L68 140 L73 85 L93 100 L98 130 L110 130 L112 108 L118 120 L125 95 L130 105 L138 85 L143 60 L145 95 L152 85 L160 115 L168 120 L175 150 L182 140 L190 150 L195 135 L202 145 L210 120 L225 105 L232 125 L245 130 L255 155 L265 165 L272 170 L280 160 L285 170 L290 165 L300 175 L310 180 L320 175 L330 185 L340 155 L345 180 L355 170 L360 175 L375 155 L390 125 L403 95 L403 224 L0 224 Z"/>
    </svg>
  </div>
  <span class="axis-label" style="left:752px;top:462px">2014</span>
  <span class="axis-label" style="left:1065px;top:462px">2019</span>

  <section class="stats">
    <div class="stats-header">Stats<span class="stats-caret"></span></div>
    <div class="stats-table">
      <div class="stat-row">Stat 1<span class="stat-value positive">0.5</span></div>
      <div class="stat-row">Stat 2<span class="stat-value negative">-3</span></div>
      <div class="stat-row">Stat 3<span class="stat-value positive">30%</span></div>
    </div>
  </section>
</div>
</body>
</html>
```